Business Card Design for a Software Startup

We'd like to have a business card design. We already have a logo. Basically what we need is a clean design with name, address, cellphone and phone numbers, e-mail and web site address (front) and a space on the back with our logo with the company name on the right side and some texts on the bottom.
We are a development and consulting company in Brazil with highly qualified team of professionals in Java, iOS and Android development and consulting.

Target Market(s)

CIO, IT managers of mid to big size companies

Industry/Entity Type

Business

```html
<!DOCTYPE html>
<html lang="en">
<head>
<meta charset="utf-8">
<title>Vantro Business Card</title>
<link rel="stylesheet" href="https://fonts.googleapis.com/css2?family=Jost:wght@400;600&family=Open+Sans:wght@400;600&display=swap">
<style>
  :root {
    --bg: #e9eaee;
    --card: #ffffff;
    --navy: #0b3a66;
    --sky: #1aa3dc;
    --ink: #2b2b2b;
    --muted: #555a60;
  }
  * { box-sizing: border-box; margin: 0; padding: 0; }
  html, body { width: 1200px; height: 987px; overflow: hidden; }
  body {
    background: var(--bg);
    font-family: "Open Sans", sans-serif;
    color: var(--ink);
    position: relative;
  }
  .card {
    position: absolute;
    left: 200px;
    width: 800px;
    height: 440px;
    background: var(--card);
    border-radius: 30px;
    overflow: hidden;
    box-shadow: 0 6px 18px rgba(0,0,0,0.12);
  }
  .card--front { top: 40px; }
  .card--back { top: 507px; }

  /* front */
  .brand {
    display: flex;
    align-items: center;
    gap: 14px;
  }
  .brand--front {
    position: absolute;
    left: 60px;
    width: 320px;
    top: 126px;
    justify-content: center;
  }
  .brand__square {
    width: 40px; height: 40px;
    border-radius: 8px;
    background: var(--navy);
    flex: none;
  }
  .brand__name {
    font-family: "Jost", sans-serif;
    font-weight: 600;
    font-size: 52px;
    letter-spacing: 1px;
    color: var(--navy);
    line-height: 1;
    white-space: nowrap;
  }
  .divider {
    position: absolute;
    left: 408px;
    top: 40px;
    width: 2px;
    height: 240px;
    background: linear-gradient(to bottom, rgba(150,150,150,0), #9aa0a6 50%, rgba(150,150,150,0));
  }
  .person {
    position: absolute;
    left: 440px;
    top: 56px;
  }
  .person__name {
    font-family: "Jost", sans-serif;
    font-weight: 600;
    font-size: 36px;
    color: var(--navy);
    line-height: 1.05;
  }
  .person__title {
    font-family: "Jost", sans-serif;
    font-size: 22px;
    color: var(--muted);
    margin-top: 2px;
  }
  .contacts {
    position: absolute;
    left: 440px;
    top: 150px;
    list-style: none;
  }
  .contacts li {
    display: flex;
    align-items: center;
    gap: 10px;
    font-size: 21px;
    color: var(--ink);
    line-height: 31px;
    white-space: nowrap;
  }
  .contacts svg { width: 16px; height: 16px; flex: none; }
  .address-band {
    position: absolute;
    left: 0; right: 0;
    top: 320px;
    height: 56px;
    background: var(--navy);
    border-top: 3px solid var(--card);
    display: flex;
    align-items: center;
    padding-left: 40px;
    font-family: "Jost", sans-serif;
    font-size: 22px;
    letter-spacing: 1px;
    color: #ffffff;
    white-space: nowrap;
  }
  .address-rule {
    position: absolute;
    left: 0; right: 0;
    height: 2px;
    background: var(--sky);
  }
  .address-rule--top { top: 314px; }
  .address-rule--bottom { top: 384px; }

  /* back */
  .brand--back {
    position: absolute;
    left: 0; right: 0;
    top: 150px;
    justify-content: center;
    gap: 20px;
  }
  .brand--back .brand__square { width: 60px; height: 60px; border-radius: 10px; }
  .brand--back .brand__name { font-size: 84px; }
  .back-url {
    position: absolute;
    left: 0; right: 0;
    top: 300px;
    text-align: center;
    font-family: "Jost", sans-serif;
    font-weight: 600;
    font-size: 24px;
    letter-spacing: 8px;
    color: #444;
  }
</style>
</head>
<body>

<section class="card card--front">
  <div class="brand brand--front">
    <span class="brand__square"></span>
    <span class="brand__name">VANTRO</span>
  </div>

  <div class="divider"></div>

  <div class="person">
    <p class="person__name">Your Name</p>
    <p class="person__title">Title</p>
  </div>

  <ul class="contacts">
    <li>
      <svg viewBox="0 0 16 16" aria-hidden="true"><circle cx="8" cy="8" r="7.2" fill="none" stroke="#0b3a66" stroke-width="1.4"/><path d="M5.2 4.6l1.4-.4.8 1.8-.9.7c.4 1 1.2 1.8 2.2 2.2l.7-.9 1.8.8-.4 1.4c-3 .2-5.8-2.6-5.6-5.6z" fill="#0b3a66"/></svg>
      123-456-7890
    </li>
    <li>
      <svg viewBox="0 0 16 16" aria-hidden="true"><rect x="4" y="1" width="8" height="14" rx="1.5" fill="#0b3a66"/><rect x="5.3" y="2.8" width="5.4" height="5" fill="#fff"/><circle cx="8" cy="12" r="1" fill="#fff"/></svg>
      456-085-4321
    </li>
    <li>
      <svg viewBox="0 0 16 16" aria-hidden="true"><rect x="1" y="3.5" width="14" height="9" rx="1" fill="#0b3a66"/><path d="M1.5 4l6.5 5 6.5-5" fill="none" stroke="#fff" stroke-width="1.2"/></svg>
      yourname@vantro.com
    </li>
    <li>
      <svg viewBox="0 0 16 16" aria-hidden="true"><circle cx="8" cy="8" r="7" fill="#0b3a66"/><path d="M1 8h14M8 1v14M3 4.5h10M3 11.5h10" stroke="#fff" stroke-width="0.9" fill="none"/><ellipse cx="8" cy="8" rx="3" ry="7" fill="none" stroke="#fff" stroke-width="0.9"/></svg>
      www.vantro.com
    </li>
  </ul>

  <div class="address-rule address-rule--top"></div>
  <div class="address-band">Door No. Street Name City Name, State, Zip Code.</div>
  <div class="address-rule address-rule--bottom"></div>
</section>

<section class="card card--back">
  <div class="brand brand--back">
    <span class="brand__square"></span>
    <span class="brand__name">VANTRO</span>
  </div>
  <p class="back-url">www.vantro.com</p>
</section>

</body>
</html>
```